Structural Engineering Business Card

Brookvane Drafting does residential house plans for clients in Central Florida. Would like simple but elegant business card that is appropriate for a house plan engineering company. Prefer black business card with black/white them but open to other shades of blue. I uploaded a sample card that I came across that looked good but please come up with your own creative designs.

Contact Information for Business Card

Name, Title, Phone, Email, Address, website

```html
<!DOCTYPE html>
<html lang="en">
<head>
<meta charset="utf-8">
<title>Brookvane Drafting – Business Card</title>
<link rel="stylesheet" href="https://fonts.googleapis.com/css2?family=Montserrat:wght@500;800&family=Arimo:wght@400&display=swap">
<style>
  :root {
    --stage: #2b2b2b;
    --ink: #0a0a0a;
    --paper: #ffffff;
    --muted: #cfcfcf;
  }
  * { box-sizing: border-box; margin: 0; padding: 0; }
  html, body { width: 1200px; height: 1015px; overflow: hidden; }
  body {
    background: var(--stage);
    font-family: "Arimo", Arial, sans-serif;
    position: relative;
  }
  .card {
    position: absolute;
    left: 320px;
    width: 560px;
    height: 320px;
    overflow: hidden;
    box-shadow: 0 10px 30px rgba(0,0,0,.45);
  }
  .card--back { top: 95px; background: var(--ink); }
  .card--front { top: 520px; background: var(--paper); }

  .wordmark {
    display: flex;
    align-items: center;
    gap: 12px;
    font-family: "Montserrat", Arial, sans-serif;
    font-weight: 800;
    font-size: 34px;
    letter-spacing: .5px;
    text-transform: uppercase;
  }
  .wordmark__square { width: 22px; height: 22px; flex: none; }

  .card--back .wordmark {
    position: absolute; inset: 0; justify-content: center; color: var(--paper);
  }
  .card--back .wordmark__square { background: var(--paper); }

  .front__logo {
    height: 150px; justify-content: center; color: var(--ink);
  }
  .front__logo .wordmark__square { background: var(--ink); }

  .front__band {
    position: absolute; left: 0; right: 0; top: 150px; height: 110px;
    background: var(--ink); color: var(--paper);
    display: flex; align-items: center;
  }
  .person { width: 50%; text-align: right; padding-right: 22px; }
  .person__name {
    font-family: "Montserrat", Arial, sans-serif; font-weight: 800; font-size: 19px;
  }
  .person__title { font-size: 14px; margin-top: 2px; }
  .band__divider { width: 1px; height: 62px; background: var(--paper); }
  .contacts { padding-left: 22px; list-style: none; font-size: 14px; line-height: 22px; }
  .contacts li { display: flex; align-items: center; gap: 9px; }
  .contacts svg { width: 13px; height: 13px; flex: none; }

  .front__address {
    position: absolute; left: 0; right: 0; top: 260px; height: 60px;
    display: flex; align-items: center; justify-content: center;
    font-size: 15px; color: var(--ink);
  }
</style>
</head>
<body>
  <section class="card card--back">
    <div class="wordmark"><span class="wordmark__square"></span>Brookvane Drafting</div>
  </section>

  <section class="card card--front">
    <div class="wordmark front__logo"><span class="wordmark__square"></span>Brookvane Drafting</div>

    <div class="front__band">
      <div class="person">
        <p class="person__name">DANIEL WHITMORE</p>
        <p class="person__title">Managing Director</p>
      </div>
      <span class="band__divider"></span>
      <ul class="contacts">
        <li>
          <svg viewBox="0 0 24 24" fill="none" stroke="#fff" stroke-width="2.2"><path d="M5 3h4l2 5-2.5 1.5a11 11 0 0 0 6 6L16 13l5 2v4a2 2 0 0 1-2 2A16 16 0 0 1 3 5a2 2 0 0 1 2-2z"/></svg>
          044-555 018 274
        </li>
        <li>
          <svg viewBox="0 0 24 24" fill="none" stroke="#fff" stroke-width="2"><rect x="2" y="5" width="20" height="14"/><path d="M2 5l10 8 10-8"/></svg>
          info@brookvane.com
        </li>
        <li>
          <svg viewBox="0 0 24 24" fill="none" stroke="#fff" stroke-width="2"><circle cx="12" cy="12" r="10"/><path d="M2 12h20M12 2c3 3 3 17 0 20M12 2c-3 3-3 17 0 20"/></svg>
          www.brookvane.com
        </li>
      </ul>
    </div>

    <p class="front__address">421, Cypress Lane, Orlando 32801, USA</p>
  </section>
</body>
</html>
```